Business Card Design

We would like to re-design our business cards. Our Company - Qwinrel Turbochargers, rebuilds turbochargers and sells replacement parts. Our website is: http://www.qwinrelturbochargers-example.com
We just had our logo changed. I will attach the file. Looking for fresh new/modern business card. We like the colors red, black, white and silver. Black background looks attractive, but not a requirement. The final design should communicate reasonable/competitive prices, top quality and reliability of our products.
Updates
Project Deadline Extended
Reason: Need to finalize the info on the card. Currently working on changing address and email info. Want to make sure it is the correct one before accepting the final design. Unless, this is something that can be changed at a later time..??
Industry/Entity Type
Business
Contact Information for Business Card
QWINREL TURBOCHARGERS, LLC
20473 Harwick Lane NE
Massillon, OH 44647
Tel: +1-555-214-7390
Fax: +1-555-267-1842
info@QwinrelTurbochargers-example.com
Our current business card had the following highlights:
*We rebuild all Turbocharges for Automotive, Diesel and Industrial
*Precision Balancing and in-house turbocharger needs
*All Turbocharger replacement parts are made in USA / U.K.
Look and feel
Each slider illustrates characteristics of the customer's brand and the style your logo design should communicate.

```html
<!DOCTYPE html>
<html lang="en">
<head>
<meta charset="utf-8">
<title>Qwinrel Turbochargers – Business Card</title>
<link rel="stylesheet" href="https://fonts.googleapis.com/css2?family=Open+Sans:wght@400;600;700&display=swap">
<style>
  :root {
    --backdrop: #d9d9d9;
    --card-black: #050505;
    --strip-dark: #141414;
    --brand-red: #e8202a;
    --white: #ffffff;
    --text-light: #f2f2f2;
  }
  * { box-sizing: border-box; margin: 0; padding: 0; }
  html, body {
    width: 1200px; height: 900px; overflow: hidden;
    background: var(--backdrop);
    font-family: "Open Sans", Arial, sans-serif;
  }
  .sheet {
    width: 1200px; height: 900px;
    display: flex; flex-direction: column; align-items: center; justify-content: center;
    gap: 40px;
  }
  .card {
    position: relative;
    width: 700px; height: 400px;
    background: var(--card-black);
    overflow: hidden;
    box-shadow: 0 6px 18px rgba(0,0,0,0.18);
  }
  .card__stripe {
    position: absolute; left: 0; right: 0; bottom: 46px; height: 9px;
    background: var(--white);
  }
  .card__band {
    position: absolute; left: 0; right: 0; bottom: 0; height: 46px;
    background: var(--brand-red);
  }
  .brand {
    display: flex; align-items: center; gap: 12px;
    color: var(--white); font-weight: 700; letter-spacing: 0.2px;
  }
  .brand__dot {
    width: 30px; height: 30px; border-radius: 50%;
    background: var(--brand-red); flex: none;
  }
  .card--front .brand {
    position: absolute; left: 50%; top: 150px; transform: translateX(-50%);
    font-size: 30px; white-space: nowrap;
  }
  .card--back .brand {
    position: absolute; left: 60px; top: 110px; font-size: 24px; white-space: nowrap;
  }
  .card--back .brand__dot { width: 24px; height: 24px; }
  .person {
    position: absolute; right: 50px; top: 90px; text-align: right;
  }
  .person__name {
    color: var(--brand-red); font-size: 22px; font-weight: 600; letter-spacing: 0.8px;
    text-transform: uppercase;
  }
  .person__role { color: var(--white); font-size: 17px; margin-top: 2px; }
  .contact-strip {
    position: absolute; left: 0; right: 0; top: 200px; bottom: 55px;
    background: var(--strip-dark);
    display: grid; grid-template-columns: 230px 170px 1fr;
    padding: 28px 0 0 50px;
    color: var(--text-light); font-size: 15.5px; line-height: 1.6;
  }
  .contact-item { display: flex; align-items: center; gap: 8px; white-space: nowrap; }
  .contact-item svg { width: 13px; height: 13px; fill: var(--brand-red); flex: none; }
  .contact-col--address .contact-item { align-items: flex-start; }
  .contact-col--address .contact-item svg { margin-top: 6px; }
  .contact-col--phones { padding-top: 28px; }
  .contact-col--web { padding-top: 50px; }
</style>
</head>
<body>
<main class="sheet">

  <section class="card card--front" aria-label="Card front">
    <div class="brand"><span class="brand__dot"></span><span>Qwinrel Turbochargers</span></div>
    <div class="card__stripe"></div>
    <div class="card__band"></div>
  </section>

  <section class="card card--back" aria-label="Card back">
    <div class="brand"><span class="brand__dot"></span><span>Qwinrel Turbochargers</span></div>
    <div class="person">
      <p class="person__name">Dorian Vessel</p>
      <p class="person__role">Managing Director</p>
    </div>

    <div class="contact-strip">
      <div class="contact-col contact-col--address">
        <p class="contact-item">
          <svg viewBox="0 0 12 12"><path d="M6 0a4 4 0 0 0-4 4c0 3 4 8 4 8s4-5 4-8a4 4 0 0 0-4-4zm0 5.6A1.6 1.6 0 1 1 6 2.4a1.6 1.6 0 0 1 0 3.2z"/></svg>
          <span>1234, Address Goes Here,<br>Country Name, 123456</span>
        </p>
      </div>
      <div class="contact-col contact-col--phones">
        <p class="contact-item">
          <svg viewBox="0 0 12 12"><path d="M1 4c0-2 2-3 5-3s5 1 5 3H8.5V3h-5v1zM3 5h6l2 5H1z"/></svg>
          <span>123.456.7890</span>
        </p>
        <p class="contact-item">
          <svg viewBox="0 0 12 12"><path d="M3 1h6v3H3zM1 5h10v5H9V8H3v2H1zM4 9h4v3H4z"/></svg>
          <span>123.456.7890</span>
        </p>
      </div>
      <div class="contact-col contact-col--web">
        <p class="contact-item">
          <svg viewBox="0 0 12 12"><path d="M0 2h12v1L6 7 0 3zM0 4.4l6 4 6-4V10H0z"/></svg>
          <span>info@youremail.com</span>
        </p>
        <p class="contact-item">
          <svg viewBox="0 0 12 12"><path d="M5 7l2-2M4.5 5L2.6 6.9a1.8 1.8 0 0 0 2.5 2.5L7 7.5M7.5 7l1.9-1.9a1.8 1.8 0 0 0-2.5-2.5L5 4.5" stroke="#e8202a" stroke-width="1.4" fill="none" stroke-linecap="round"/></svg>
          <span>www.website.com</span>
        </p>
      </div>
    </div>

    <div class="card__stripe"></div>
    <div class="card__band"></div>
  </section>

</main>
</body>
</html>
```